Velvette by Marisa Dunn business cards

I am after a business card that will fit the name of my business - velvette.
I want something classy and sexy and nothing tacky.
Ideas that I like are Zebra print backgrounds glitter back grounds
Two ideas I had were
1. Zebra print in black and white, the name Velvette by Marisa Dunn and a shilouette of a woman laying on top of the name. Or instead of zebra a glitter background.
2. Idea very similar except for instead of a woman a pair of lips maybe a hot pink glitter or a gold glitter depending on background with the business name between the lips.
Or you can do something completely different.

```html
<!DOCTYPE html>
<html lang="en">
<head>
<meta charset="utf-8">
<title>Velvette by Marisa Dunn – Business Cards</title>
<link href="https://fonts.googleapis.com/css2?family=Didact+Gothic&family=Montserrat:wght@700&display=swap" rel="stylesheet">
<style>
  :root {
    --bg: #e4e4e2;
    --yellow-light: #fff200;
    --yellow-deep: #f6c600;
    --ink: #1c1a16;
    --band: #2b2a27;
    --band-text: #9a9890;
    --stripe-dark: #1e1b14;
    --stripe-warm: #7a5c08;
  }
  * { box-sizing: border-box; margin: 0; padding: 0; }
  html, body { width: 1200px; height: 873px; overflow: hidden; }
  body {
    background: var(--bg);
    font-family: "Didact Gothic", "Century Gothic", sans-serif;
    color: var(--ink);
    position: relative;
  }
  .card {
    position: absolute;
    top: 156px;
    width: 340px;
    height: 560px;
    background: radial-gradient(circle at 55% 40%, var(--yellow-light) 0%, var(--yellow-deep) 100%);
    box-shadow: 0 10px 28px rgba(0,0,0,0.18);
    overflow: hidden;
  }
  .card--front { left: 210px; }
  .card--back { left: 650px; }

  /* Front */
  .brand {
    position: absolute;
    top: 150px;
    left: 0;
    width: 100%;
    text-align: center;
  }
  .brand__mark {
    display: block;
    width: 64px;
    height: 64px;
    margin: 0 auto 26px;
    border: 3px solid var(--ink);
  }
  .brand__name {
    font-size: 56px;
    letter-spacing: 2px;
    line-height: 1;
  }
  .brand__by {
    font-size: 20px;
    margin-top: 12px;
    letter-spacing: 1px;
  }
  .web-band {
    position: absolute;
    left: 0;
    bottom: 0;
    width: 100%;
    height: 44px;
    background: var(--band);
    color: var(--band-text);
    font-size: 15px;
    letter-spacing: 0.5px;
    display: flex;
    align-items: center;
    justify-content: center;
  }

  /* Back */
  .holder {
    position: absolute;
    top: 60px;
    left: 34px;
    width: 272px;
  }
  .holder__name {
    font-family: "Montserrat", sans-serif;
    font-weight: 700;
    font-size: 22px;
    line-height: 1;
  }
  .holder__rule {
    height: 3px;
    margin: 4px 0 3px;
    background: linear-gradient(90deg, var(--ink) 0%, var(--ink) 55%, rgba(28,26,22,0) 100%);
  }
  .holder__role { font-size: 16px; }
  .contact {
    position: absolute;
    top: 128px;
    right: 30px;
    text-align: right;
    font-size: 15.5px;
    line-height: 1.55;
    font-style: normal;
  }
  .contact__gap { margin-top: 14px; }
  .contact__email {
    position: absolute;
    top: 300px;
    right: 30px;
    font-size: 15.5px;
  }
  .stripe-field {
    position: absolute;
    left: 0;
    bottom: 0;
    width: 100%;
    height: 210px;
    background: linear-gradient(165deg, var(--stripe-warm) 0%, var(--stripe-dark) 70%);
    clip-path: polygon(0 28%, 100% 0, 100% 100%, 0 100%);
  }
</style>
</head>
<body>
  <section class="card card--front" aria-label="Card front">
    <div class="brand">
      <span class="brand__mark"></span>
      <div class="brand__name">Velvette</div>
      <div class="brand__by">by Marisa Dunn</div>
    </div>
    <div class="web-band">www.velvettebymarisadunn.com</div>
  </section>

  <section class="card card--back" aria-label="Card back">
    <div class="holder">
      <div class="holder__name">Marisa Dunn</div>
      <div class="holder__rule"></div>
      <div class="holder__role">Proprietor</div>
    </div>
    <address class="contact">
      <div>18, Larchmont Ave</div>
      <div>Pasadena, CA 91101</div>
      <div class="contact__gap">555014273</div>
      <div class="contact__gap">555098612</div>
    </address>
    <div class="contact__email">velvettebymd@velvettebymd.com</div>
    <div class="stripe-field" role="img" aria-label="Black and gold zebra stripe pattern"></div>
  </section>
</body>
</html>
```